Stonebridge Building and Projects business cards

A business card with watermark background (construction work)

Company logo attached

Home improvement projects
House renovations
Bathroom and kitchen renovations
House extensions
New builds and granny flats

Director Omar Haddani
(Phone number)
omar@sbpbuilding.com.au
(Instagram logo) sbp_building

```html
<!DOCTYPE html>
<html lang="en">
<head>
<meta charset="utf-8">
<title>Stonebridge Building and Projects – Business Cards</title>
<link rel="stylesheet" href="https://fonts.googleapis.com/css2?family=Montserrat:wght@600&family=Roboto:wght@400&family=Cutive&display=swap">
<style>
  :root {
    --brand-blue: #3177b6;
    --ink: #333333;
    --paper: #ffffff;
    --backdrop: #e4e4e4;
  }
  * { margin: 0; padding: 0; box-sizing: border-box; }
  html, body { width: 1200px; height: 900px; overflow: hidden; background: var(--backdrop); }
  .canvas { position: relative; width: 1200px; height: 900px; }

  .card {
    position: absolute; top: 216px; width: 309px; height: 501px;
    box-shadow: 2px 2px 3px rgba(0,0,0,0.45);
  }
  .card--front { left: 279px; background: var(--brand-blue); color: var(--paper); border-radius: 0 66px 0 66px; }
  .card--back { left: 617px; background: var(--paper); color: var(--ink); border-radius: 66px 0 66px 0; }

  .wordmark { position: absolute; left: 0; right: 0; text-align: center; font-family: 'Montserrat', sans-serif; font-weight: 600; }
  .card--front .wordmark { top: 120px; color: var(--paper); }
  .card--back .wordmark { top: 62px; color: var(--brand-blue); }
  .wordmark__mark { display: block; width: 22px; height: 22px; margin: 0 auto 12px; background: currentColor; }
  .wordmark__name { display: block; font-size: 27px; line-height: 1.1; }
  .wordmark__sub { display: block; font-size: 13.5px; line-height: 1.4; letter-spacing: 0.5px; }

  .tagline {
    position: absolute; left: 50%; transform: translateX(-50%); white-space: nowrap;
    font-family: 'Cutive', serif; font-size: 14.5px; padding: 0 4px 2px;
    border-bottom: 1.5px solid currentColor;
  }
  .card--front .tagline { top: 272px; color: var(--paper); }
  .card--back .tagline { top: 214px; color: var(--brand-blue); }

  .services {
    position: absolute; top: 367px; left: 0; right: 0; list-style: none; text-align: center;
    font-family: 'Roboto', sans-serif; font-size: 14.4px; line-height: 18px;
  }

  .person { position: absolute; left: 33px; top: 316px; }
  .person__name { font-family: 'Montserrat', sans-serif; font-weight: 600; font-size: 20px; color: var(--brand-blue); line-height: 1.2; }
  .person__role { font-family: 'Roboto', sans-serif; font-size: 14px; line-height: 1.2; }

  .contacts { position: absolute; left: 33px; top: 368px; list-style: none; font-family: 'Roboto', sans-serif; font-size: 14px; }
  .contacts li { display: flex; align-items: center; height: 18px; }
  .contacts li.contacts__social { margin-top: 13px; }
  .contacts svg { width: 13px; height: 13px; margin-right: 5px; fill: var(--brand-blue); flex: none; }
  .contacts .accent { color: var(--brand-blue); }
  .social-square { width: 16px; height: 16px; background: var(--brand-blue); border-radius: 3px; margin-right: 6px; flex: none; }
</style>
</head>
<body>
<div class="canvas">

  <section class="card card--front">
    <div class="wordmark">
      <span class="wordmark__mark"></span>
      <span class="wordmark__name">Stonebridge</span>
      <span class="wordmark__sub">Building and Projects</span>
    </div>
    <p class="tagline">Built right, start to finish!</p>
    <ul class="services">
      <li>Home improvement projects</li>
      <li>House renovations</li>
      <li>Bathroom and kitchen renovations</li>
      <li>House extensions</li>
      <li>New builds and granny flats</li>
    </ul>
  </section>

  <section class="card card--back">
    <div class="wordmark">
      <span class="wordmark__mark"></span>
      <span class="wordmark__name">Stonebridge</span>
      <span class="wordmark__sub">Building and Projects</span>
    </div>
    <p class="tagline">Built right, start to finish!</p>

    <div class="person">
      <p class="person__name">Omar Haddani</p>
      <p class="person__role">Director</p>
    </div>

    <ul class="contacts">
      <li>
        <svg viewBox="0 0 24 24" aria-hidden="true"><path d="M6.6 10.8a15.1 15.1 0 0 0 6.6 6.6l2.2-2.2c.3-.3.7-.4 1-.2 1.1.4 2.3.6 3.6.6.6 0 1 .4 1 1V20c0 .6-.4 1-1 1C10.6 21 3 13.4 3 4c0-.6.4-1 1-1h3.5c.6 0 1 .4 1 1 0 1.3.2 2.5.6 3.6.1.3 0 .7-.2 1z"/></svg>
        041-555 208 614
      </li>
      <li>
        <svg viewBox="0 0 24 24" aria-hidden="true"><path d="M2 5h20v14H2zM3.5 6.5 12 13l8.5-6.5v1.8L12 14.8 3.5 8.3z" fill-rule="evenodd"/></svg>
        omar@sbpbuilding.com.au
      </li>
      <li>
        <svg viewBox="0 0 24 24" aria-hidden="true"><path d="M12 2a10 10 0 1 0 0 20 10 10 0 0 0 0-20zm0 1.6c.9 0 2.1 1.7 2.7 4.4H9.3c.6-2.7 1.8-4.4 2.7-4.4zM3.6 12c0-1 .2-1.8.5-2.6h3.7a18 18 0 0 0 0 5.2H4.1c-.3-.8-.5-1.6-.5-2.6zm5.5 0c0-.9.1-1.8.2-2.6h5.4a17 17 0 0 1 0 5.2H9.3c-.1-.8-.2-1.7-.2-2.6zm7.1 2.6a18 18 0 0 0 0-5.2h3.7a8.4 8.4 0 0 1 0 5.2zM12 20.4c-.9 0-2.1-1.7-2.7-4.4h5.4c-.6 2.7-1.8 4.4-2.7 4.4z"/></svg>
        www.<span class="accent">sbpbuilding</span>.com.au
      </li>
      <li class="contacts__social">
        <span class="social-square"></span>
        sbp_building
      </li>
    </ul>
  </section>

</div>
</body>
</html>
```